Moravel Aesthetic Doctor

I require an elegant, luxurious looking business card for my aesthetic business. I am a doctor and that will set me aside from competitors. I am planning to provide home and spa based treatments to clients with high expectations. I have attached my logo.

```html
<!DOCTYPE html>
<html lang="en">
<head>
<meta charset="utf-8">
<title>Moravel Aesthetic Doctor – Business Card</title>
<link href="https://fonts.googleapis.com/css2?family=Roboto:wght@300;400&family=Rajdhani:wght@600&display=swap" rel="stylesheet">
<style>
  :root {
    --backdrop: #bdbdbd;
    --card: #f1f1f1;
    --card-edge: #e4e4e4;
    --ink: #2b2b2b;
    --slate: #7d8694;
    --blue: #2f8fd0;
    --blue-deep: #1465a8;
    --blue-light: #5ab0e0;
    --rule: #a9adb3;
    --white: #ffffff;
  }
  * { box-sizing: border-box; margin: 0; padding: 0; }
  html, body { width: 1200px; height: 576px; overflow: hidden; }
  body {
    background: var(--backdrop);
    font-family: "Roboto", Arial, sans-serif;
    position: relative;
  }
  .card {
    position: absolute;
    background: linear-gradient(180deg, var(--white) 0%, var(--card) 55%, var(--card-edge) 100%);
    border-radius: 10px;
    overflow: hidden;
    box-shadow: 0 3px 6px rgba(0,0,0,0.25);
  }
  .card--front { left: 82px; top: 139px; width: 484px; height: 293px; }
  .card--back  { left: 602px; top: 138px; width: 481px; height: 292px; }

  .brand {
    position: absolute;
    display: flex;
    align-items: center;
    gap: 12px;
    font-weight: 300;
    color: var(--slate);
    letter-spacing: 0.5px;
    white-space: nowrap;
  }
  .brand__dot {
    width: 46px; height: 46px;
    border-radius: 50%;
    background: var(--blue);
    flex: none;
  }
  .card--front .brand { left: 0; right: 0; justify-content: center; top: 82px; font-size: 27px; }
  .card--back .brand { left: 18px; top: 48px; font-size: 25px; }
  .card--back .brand__dot { width: 42px; height: 42px; }

  .services {
    position: absolute;
    left: 0; right: 0; top: 196px;
    text-align: center;
    font-size: 13px;
    line-height: 19px;
    color: var(--ink);
  }
  .services .sep { color: var(--blue); margin: 0 6px; }

  .band {
    position: absolute;
    left: 0; right: 0; top: 239px; height: 35px;
    background: linear-gradient(90deg, var(--blue-deep) 0%, var(--blue) 55%, var(--blue-light) 100%);
    color: var(--white);
    font-size: 12.5px;
    letter-spacing: 0.8px;
    display: flex; align-items: center; justify-content: center;
  }

  .doctor {
    position: absolute;
    left: 23px; right: 32px; top: 168px;
    display: flex; align-items: baseline; gap: 6px;
  }
  .doctor__name {
    font-family: "Rajdhani", "Arial Narrow", sans-serif;
    font-weight: 600;
    font-size: 18px;
    color: var(--ink);
  }
  .doctor__post { font-size: 10px; color: var(--blue); }
  .doctor__rule { flex: 1; height: 1px; background: var(--rule); align-self: center; margin-top: 4px; }

  .qualification {
    position: absolute; left: 23px; top: 191px;
    font-size: 13px; color: var(--blue);
  }
  .contacts {
    position: absolute; left: 23px; top: 220px;
    display: flex; gap: 14px;
    font-size: 12.5px; color: var(--ink);
  }
  .contacts__item { display: flex; align-items: center; gap: 6px; }
  .contacts__item svg { width: 12px; height: 12px; fill: none; stroke: var(--slate); stroke-width: 1.6; }
  .contacts .accent { color: var(--blue); }
  .follow {
    position: absolute; left: 23px; top: 242px;
    display: flex; align-items: center; gap: 4px;
    font-size: 12.5px; color: var(--ink);
  }
  .follow__dot { width: 13px; height: 13px; border-radius: 50%; background: var(--blue); margin-left: 2px; }

  .tab {
    position: absolute; right: 0; bottom: 0;
    width: 264px; height: 36px;
  }
  .tab svg { position: absolute; inset: 0; width: 100%; height: 100%; }
  .tab__text {
    position: absolute; right: 22px; top: 0; bottom: 0;
    display: flex; align-items: center;
    font-size: 12px; color: var(--white);
  }
</style>
</head>
<body>

<section class="card card--front">
  <div class="brand"><span class="brand__dot"></span>Moravel Aesthetic Doctor</div>
  <p class="services">
    Dermal Injectables<span class="sep">|</span>Plasma Facials<span class="sep">|</span>Microneedling<br>
    Skin Boosters<span class="sep">|</span>Excessive Sweating
  </p>
  <div class="band">HOME AND SPA BASED TREATMENTS</div>
</section>

<section class="card card--back">
  <div class="brand"><span class="brand__dot"></span>Moravel Aesthetic Doctor</div>

  <div class="doctor">
    <span class="doctor__name">Dr Liesel Marwick</span>
    <span class="doctor__post">MRCPCH MD</span>
    <span class="doctor__rule"></span>
  </div>
  <p class="qualification">Australasian Diploma of Aesthetic Medicine</p>

  <div class="contacts">
    <span class="contacts__item">
      <svg viewBox="0 0 12 12"><path d="M2 1.5h2.2l1 2.5-1.3 1a6 6 0 0 0 3.1 3.1l1-1.3 2.5 1V10a1 1 0 0 1-1 1A9 9 0 0 1 1 2.5a1 1 0 0 1 1-1z" fill="var(--slate)" stroke="none"/></svg>
      0800 555 014
    </span>
    <span class="contacts__item">
      <svg viewBox="0 0 12 12"><rect x="1" y="2.5" width="10" height="7"/><path d="M1 2.5l5 4 5-4"/></svg>
      liesel@moravel.co.nz
    </span>
    <span class="contacts__item">
      <svg viewBox="0 0 12 12"><circle cx="6" cy="6" r="4.7"/><ellipse cx="6" cy="6" rx="2" ry="4.7"/><path d="M1.3 6h9.4"/></svg>
      <span>www.<span class="accent">moravel</span>.co.nz</span>
    </span>
  </div>
  <div class="follow">Follow us on:<span class="follow__dot"></span><span class="follow__dot"></span></div>

  <div class="tab">
    <svg viewBox="0 0 264 36" preserveAspectRatio="none"><path d="M22 0H264V36H0z" fill="var(--blue-light)"/></svg>
    <span class="tab__text">Home &amp; Spa Based Treatments</span>
  </div>
</section>

</body>
</html>
```